6"x9" Postcard Mailer

A 6"x9" Postcard mailer targeted to forensic laboratories to advertise or mock forensic samples (https://veltrascience.example/products/mock-forensic-samples/).

Here is some copy, but we can modify if there is not enough space:

Headline:
Expedite Training, Validation, & R&D with Our Ready-to-Use Mock Samples

Bullet Points:

- Wide Variety of Sample Types: IRB-approved samples mimicking crime scene substances, including semen, hair, bone, saliva, blood, and vaginal epithelial cells.
- Diverse Scenarios: Simulate sexual assault and degraded samples for varied conditions.
- Custom Solutions: Tailored DNA quantities and concentrations to suit your lab's needs.

Use discount code TRAL47 for a 10% discount

```html
<!DOCTYPE html>
<html lang="en">
<head>
<meta charset="utf-8">
<title>Veltra Science – Mock Samples Postcard</title>
<link rel="stylesheet" href="https://fonts.googleapis.com/css2?family=Poppins:wght@400;500;600;700;800&display=swap">
<style>
  :root{
    --navy:#1c2a4b;
    --navy-deep:#16223f;
    --blue:#1e6fc6;
    --sky:#5aaee0;
    --sky-soft:#79c0ea;
    --banner:#3a3d42;
    --white:#ffffff;
    --page:#d8d8d8;
    --stamp:#e6e6e6;
    --ink-muted:#5b7fb8;
  }
  *{box-sizing:border-box;margin:0;padding:0}
  html,body{width:874px;height:1200px;overflow:hidden;background:var(--page);font-family:"Poppins",sans-serif}
  .postcard{position:absolute;left:37px;width:800px;height:533px;overflow:hidden;background:var(--white);box-shadow:0 4px 10px rgba(0,0,0,.25)}
  .postcard--front{top:40px}
  .postcard--back{top:627px}
  .card-shapes{position:absolute;inset:0;width:800px;height:533px}
  .brand{position:absolute;display:flex;align-items:center;gap:8px;font-weight:500;color:var(--ink-muted);letter-spacing:-.3px}
  .brand-dot{width:10px;height:10px;border-radius:50%;background:var(--sky)}
  .front-brand{left:44px;top:38px;font-size:30px}
  .headline{position:absolute;left:42px;top:114px;font-weight:800;font-size:38px;line-height:38px;letter-spacing:-.4px;text-transform:uppercase}
  .headline .hl-light{color:var(--sky)}
  .headline .hl-dark{color:var(--navy)}
  .headline .hl-amp{color:var(--ink-muted);font-weight:400}
  .headline .hl-rd{color:var(--ink-muted)}
  .tagline-banner{position:absolute;left:62px;top:290px;color:var(--white)}
  .tagline-banner .lead{display:block;font-size:19px;font-weight:400;color:var(--sky);letter-spacing:.3px;line-height:22px}
  .tagline-banner .product{display:block;font-size:29px;font-weight:800;line-height:32px}
  .discount{position:absolute;display:flex;align-items:center}
  .discount-badge{position:relative;z-index:2;width:80px;height:80px;border-radius:50%;background:var(--white);border:5px solid var(--navy-deep);box-shadow:0 0 0 3px var(--blue);display:flex;flex-direction:column;align-items:center;justify-content:center;color:var(--navy)}
  .discount-badge .pct{font-size:32px;font-weight:600;line-height:30px;letter-spacing:-2px;transform:scaleX(.82)}
  .discount-badge .lbl{font-size:9px;font-weight:500;color:var(--blue);line-height:10px}
  .discount-code{margin-left:-14px;display:flex;flex-direction:column;gap:3px}
  .discount-code .cta{background:var(--blue);color:var(--white);font-size:15px;font-weight:500;padding:0 14px 0 28px;height:21px;line-height:21px;border-radius:0 3px 3px 0}
  .discount-code .code{background:var(--sky);color:var(--navy);font-size:22px;font-weight:700;letter-spacing:4px;padding:0 14px 0 28px;height:31px;line-height:31px;border-radius:0 3px 3px 0}
  .front-discount{left:46px;top:382px}
  .front-discount .discount-code .cta,.front-discount .discount-code .code{width:210px}
  .site{position:absolute;font-size:19px;font-weight:500;letter-spacing:1.5px}
  .site b{font-weight:700;color:var(--sky)}
  .front-site{left:55px;top:480px;color:var(--white)}
  .features{position:absolute;left:40px;top:58px;list-style:none;width:300px}
  .feature{display:flex;gap:13px;margin-bottom:16px}
  .feature-icon{flex:none;width:58px;height:58px;border-radius:50%;background:var(--white);border:4px solid var(--blue);display:flex;align-items:center;justify-content:center;margin-top:4px}
  .feature-icon svg{width:30px;height:30px}
  .feature h3{font-size:14px;font-weight:700;color:var(--sky);line-height:17px}
  .feature p{font-size:14px;font-weight:400;color:var(--white);line-height:17.5px}
  .back-discount{left:44px;top:361px}
  .back-discount .discount-code .cta,.back-discount .discount-code .code{width:186px}
  .phone{position:absolute;left:45px;top:455px;display:flex;align-items:center;gap:6px;color:var(--white);font-size:27px;font-weight:700}
  .phone svg{width:20px;height:20px}
  .back-brand{left:464px;top:46px;font-size:20px}
  .stamp{position:absolute;left:680px;top:48px;width:72px;height:87px;background:var(--stamp)}
  .back-site{right:46px;top:463px;color:var(--navy);font-size:18px}
</style>
</head>
<body>

<section class="postcard postcard--front">
  <svg class="card-shapes" viewBox="0 0 800 533" aria-hidden="false">
    <defs>
      <linearGradient id="frontRing" x1="0" y1="0" x2="0" y2="1">
        <stop offset="0" stop-color="#1e6fc6"/>
        <stop offset="1" stop-color="#bfe3f6"/>
      </linearGradient>
      <linearGradient id="labPhoto" x1="0.8" y1="0" x2="0.3" y2="1">
        <stop offset="0" stop-color="#0c1120"/>
        <stop offset=".35" stop-color="#1f4fbf"/>
        <stop offset=".65" stop-color="#3c63c4"/>
        <stop offset="1" stop-color="#e2e5ec"/>
      </linearGradient>
    </defs>
    <rect width="800" height="533" fill="#ffffff"/>
    <rect y="324" width="800" height="209" fill="#1c2a4b"/>
    <path d="M62 286 H430 V356 H62 Q44 356 44 338 V304 Q44 286 62 286 Z" fill="#3a3d42"/>
    <circle cx="602" cy="262" r="294" fill="url(#frontRing)"/>
    <g role="img" aria-label="Gloved hand swabbing a blood stain with a red-capped forensic swab">
      <circle cx="608" cy="262" r="280" fill="url(#labPhoto)"/>
    </g>
  </svg>

  <div class="brand front-brand"><span class="brand-dot"></span>Veltra Science</div>

  <h1 class="headline">
    <span class="hl-light">Expedite</span><br>
    <span class="hl-light">Training,</span><br>
    <span class="hl-dark">Validation,</span><br>
    <span class="hl-amp">&amp;</span> <span class="hl-rd">R&amp;D</span>
  </h1>

  <p class="tagline-banner"><span class="lead">WITH OUR READY-TO-USE</span><span class="product">MOCK SAMPLES</span></p>

  <div class="discount front-discount">
    <div class="discount-badge"><span class="pct">10%</span><span class="lbl">DISCOUNT</span></div>
    <div class="discount-code"><span class="cta">USE DISCOUNT CODE</span><span class="code">TRAL47</span></div>
  </div>

  <p class="site front-site">www.<b>veltrascience</b>.example</p>
</section>

<section class="postcard postcard--back">
  <svg class="card-shapes" viewBox="0 0 800 533">
    <defs>
      <linearGradient id="backRing" x1="0" y1="0" x2="0" y2="1">
        <stop offset="0" stop-color="#1e6fc6"/>
        <stop offset="1" stop-color="#bfe3f6"/>
      </linearGradient>
      <linearGradient id="kitBox" x1="0" y1="0" x2="1" y2="1">
        <stop offset="0" stop-color="#e9eef5"/>
        <stop offset=".6" stop-color="#9cc0e6"/>
        <stop offset="1" stop-color="#1e5fae"/>
      </linearGradient>
    </defs>
    <rect width="800" height="533" fill="#ffffff"/>
    <circle cx="176" cy="262" r="302" fill="url(#backRing)"/>
    <circle cx="170" cy="262" r="290" fill="#1c2a4b"/>
    <g role="img" aria-label="Open product box of mock forensic sample tubes">
      <rect x="338" y="243" width="144" height="215" rx="4" fill="url(#kitBox)"/>
    </g>
  </svg>

  <ul class="features">
    <li class="feature">
      <span class="feature-icon"><svg viewBox="0 0 30 30"><rect x="11" y="3" width="8" height="3" rx="1" fill="#1c2a4b"/><path d="M12 6 V22 a3 3 0 0 0 6 0 V6" fill="none" stroke="#1c2a4b" stroke-width="2.2"/><path d="M12.5 14 H17.5 V22 a2.5 2.5 0 0 1 -5 0 Z" fill="#1c2a4b"/></svg></span>
      <div><h3>Wide Variety of Sample Types</h3><p>IRB-approved samples mimicking crime scene substances, including semen, hair, bone, saliva, blood, and vaginal epithelial cells.</p></div>
    </li>
    <li class="feature">
      <span class="feature-icon"><svg viewBox="0 0 30 30"><rect x="3" y="7" width="24" height="16" rx="5" fill="#1c2a4b"/><g fill="#ffffff"><circle cx="10" cy="12.5" r="1.8"/><circle cx="15" cy="12.5" r="1.8"/><circle cx="20" cy="12.5" r="1.8"/><circle cx="10" cy="17.5" r="1.8"/><circle cx="15" cy="17.5" r="1.8"/><circle cx="20" cy="17.5" r="1.8"/></g></svg></span>
      <div><h3>Diverse Scenarios</h3><p>Simulate sexual assault and degraded samples for varied conditions.</p></div>
    </li>
    <li class="feature">
      <span class="feature-icon"><svg viewBox="0 0 30 30" fill="none" stroke="#1c2a4b" stroke-width="2.4" stroke-linecap="round"><path d="M8 26 C 12 18, 18 12, 22 4"/><path d="M5 20 C 12 20, 18 14, 18 6"/><path d="M12 25 C 12 17, 18 11, 25 11"/><path d="M10 17 L15 21 M13 13 L18 17 M16 9 L20 13"/></svg></span>
      <div><h3>Custom Solutions</h3><p>Tailored DNA quantities and concentrations to suit your lab's needs</p></div>
    </li>
  </ul>

  <div class="discount back-discount">
    <div class="discount-badge"><span class="pct">10%</span><span class="lbl">DISCOUNT</span></div>
    <div class="discount-code"><span class="cta">USE DISCOUNT CODE</span><span class="code">TRAL47</span></div>
  </div>

  <p class="phone"><svg viewBox="0 0 24 24"><path d="M6.6 10.8a15.1 15.1 0 0 0 6.6 6.6l2.2-2.2a1 1 0 0 1 1-.25 11.4 11.4 0 0 0 3.6.57 1 1 0 0 1 1 1V20a1 1 0 0 1-1 1A17 17 0 0 1 3 4a1 1 0 0 1 1-1h3.5a1 1 0 0 1 1 1 11.4 11.4 0 0 0 .57 3.6 1 1 0 0 1-.25 1Z" fill="#5aaee0"/></svg>+1 555 014 7720</p>

  <div class="brand back-brand"><span class="brand-dot"></span>Veltra Science</div>
  <div class="stamp"></div>
  <p class="site back-site">www.<b>veltrascience</b>.example</p>
</section>

</body>
</html>
```